Australian Trucking Company Requires Professional Looking Stationary

We require a professional looking stationary design that incorporates our newly designed logo.

Our business, called "Brell Haulage Contracting", provides contracting work, transport and logistics to business in Western Australia particularly with links to the mining sector.

We are a small business looking to expand and our new logo and our new stationary will help develop our brand image in our market place.

Target Market(s)

Businesses and Corporation with links to the Mining Sector

Industry/Entity Type

Small Business

Requirements
Must have
• The letterhead must have the following details:
The new logo

Text saying: "Brell Holdings Pty Ltd (ACN 582 316 907) ATF The Brell Discretionary Trust T/AS"
"ABN 71 834 209 553"
Address "P.O Box 817 Wattlegrove WA, 6958"
Phone: 08 9352 7140
Email: brellhaul@mailbox-example.com.au

The text on the letterhead should be editable as the details are likely to change in the near future. Provision should be made for a website address all though one isn't available at the moment.

The styling, layout and font text is entirely up to the designer.

```html
<!DOCTYPE html>
<html lang="en">
<head>
<meta charset="utf-8">
<title>Brell Haulage Contracting – Letterhead Options</title>
<link href="https://fonts.googleapis.com/css2?family=Arimo:wght@400&family=PT+Sans:wght@400&family=Saira:wght@800&display=swap" rel="stylesheet">
<style>
  :root {
    --backdrop: #e8e2da;
    --paper: #ffffff;
    --brand-red: #e11d26;
    --band-red: #a3101a;
    --band-deep: #6e0a10;
    --swoosh-dark: #1c1c1c;
    --swoosh-silver: #d9d9d9;
    --contact-ink: #ffffff;
    --footer-grey: #555555;
    --footer-red: #9b1b22;
    --label-ink: #5a4a3c;
  }
  * { margin: 0; padding: 0; box-sizing: border-box; }
  html, body { width: 1200px; height: 774px; overflow: hidden; background: var(--backdrop); }
  .canvas { position: relative; width: 1200px; height: 774px; }

  .letterhead {
    position: absolute; top: 30px; width: 488px; height: 687px;
    background: var(--paper);
    box-shadow: 0 2px 8px rgba(0,0,0,.18);
    overflow: hidden;
  }
  .letterhead--one { left: 72px; }
  .letterhead--two { left: 641px; }

  .header-band { position: absolute; left: 0; top: 0; width: 488px; height: 125px; display: block; }

  .brand-name {
    position: absolute;
    font-family: "Saira", sans-serif; font-weight: 800;
    font-size: 16px; line-height: 17px; letter-spacing: .5px;
    text-transform: uppercase; color: var(--brand-red);
  }
  .letterhead--one .brand-name { left: 84px; top: 15px; }
  .letterhead--two .brand-name { left: 92px; top: 47px; }

  .contact-list {
    position: absolute; list-style: none;
    font-family: "Arimo", sans-serif; font-size: 9px; line-height: 12.5px;
    color: var(--contact-ink); text-align: right;
  }
  .letterhead--one .contact-list { right: 24px; top: 44px; }
  .letterhead--two .contact-list { right: 16px; top: 15px; }
  .contact-list li { display: flex; justify-content: flex-end; align-items: center; gap: 6px; white-space: nowrap; }
  .contact-icon { width: 8px; height: 8px; flex: none; }

  .legal-footer {
    position: absolute; left: 0; width: 100%; top: 650px;
    font-family: "PT Sans", sans-serif; font-size: 9px; line-height: 16px; text-align: center;
  }
  .legal-footer .abn { color: var(--footer-grey); }
  .legal-footer .entity { color: var(--footer-red); }

  .option-label {
    position: absolute; top: 719px; width: 488px; text-align: center;
    font-family: "PT Sans", sans-serif; font-size: 15px; color: var(--label-ink);
  }
  .option-label--one { left: 72px; }
  .option-label--two { left: 641px; }
</style>
</head>
<body>
<div class="canvas">

  <!-- Letterhead, layout one -->
  <article class="letterhead letterhead--one">
    <svg class="header-band" viewBox="0 0 488 125" aria-hidden="true">
      <defs>
        <linearGradient id="bandOne" x1="0" y1="0" x2="0" y2="1">
          <stop offset="0" stop-color="var(--band-deep)"/>
          <stop offset="1" stop-color="var(--band-red)"/>
        </linearGradient>
      </defs>
      <path d="M0,88 C180,92 260,64 320,44 S440,2 488,0 L488,115 L0,115 Z" fill="url(#bandOne)"/>
      <path d="M0,96 C180,100 262,72 324,52 S442,8 488,6" fill="none" stroke="var(--swoosh-silver)" stroke-width="2.5"/>
      <path d="M0,102 C180,106 264,78 328,58 S444,12 488,10" fill="none" stroke="var(--swoosh-dark)" stroke-width="4"/>
    </svg>
    <div class="brand-name">Brell<br>Haulage<br>Contracting</div>
    <ul class="contact-list">
      <li>08 9352 7140 <svg class="contact-icon" viewBox="0 0 8 8"><circle cx="4" cy="4" r="3.6" fill="none" stroke="#fff" stroke-width=".8"/><path d="M2.6,2 L3.4,2 L3.6,3.2 L5.6,5 L5.8,6 L4.8,6 C3,5.2 2.4,3.6 2.6,2Z" fill="#fff"/></svg></li>
      <li>brellhaul@mailbox-example.com.au <svg class="contact-icon" viewBox="0 0 8 8"><rect x=".5" y="2" width="7" height="4.5" fill="#fff"/></svg></li>
      <li>www.brellhaulage-example.com.au <svg class="contact-icon" viewBox="0 0 8 8"><circle cx="4" cy="4" r="3.3" fill="none" stroke="#fff" stroke-width=".9"/><path d="M.8,4 H7.2 M4,.8 V7.2" stroke="#fff" stroke-width=".6"/></svg></li>
      <li>P.O Box 817 Wattlegrove WA, 6958 <svg class="contact-icon" viewBox="0 0 8 8"><path d="M4,.5 L7.5,4 L6.3,4 L6.3,7.5 L1.7,7.5 L1.7,4 L.5,4 Z" fill="#fff"/></svg></li>
    </ul>
    <footer class="legal-footer">
      <p class="abn">ABN 71 834 209 553</p>
      <p class="entity">Brell Holdings Pty Ltd (ACN 582 316 907) ATF The Brell Discretionary Trust T/AS</p>
    </footer>
  </article>

  <!-- Letterhead, layout two -->
  <article class="letterhead letterhead--two">
    <svg class="header-band" viewBox="0 0 488 125" aria-hidden="true">
      <defs>
        <linearGradient id="bandTwo" x1="0" y1="0" x2="0" y2="1">
          <stop offset="0" stop-color="var(--band-red)"/>
          <stop offset="1" stop-color="var(--band-deep)"/>
        </linearGradient>
      </defs>
      <path d="M0,0 L488,0 L488,112 C380,110 300,70 200,38 C130,18 60,12 0,12 Z" fill="url(#bandTwo)"/>
      <path d="M0,18 C70,18 140,26 210,48 C310,80 390,116 488,118" fill="none" stroke="var(--swoosh-silver)" stroke-width="2.5"/>
      <path d="M0,13 C65,12 135,20 205,42 C305,74 385,112 488,114" fill="none" stroke="var(--swoosh-dark)" stroke-width="3"/>
    </svg>
    <div class="brand-name">Brell<br>Haulage<br>Contracting</div>
    <ul class="contact-list">
      <li>08 9352 7140 <svg class="contact-icon" viewBox="0 0 8 8"><circle cx="4" cy="4" r="3.6" fill="none" stroke="#fff" stroke-width=".8"/><path d="M2.6,2 L3.4,2 L3.6,3.2 L5.6,5 L5.8,6 L4.8,6 C3,5.2 2.4,3.6 2.6,2Z" fill="#fff"/></svg></li>
      <li>brellhaul@mailbox-example.com.au <svg class="contact-icon" viewBox="0 0 8 8"><rect x=".5" y="2" width="7" height="4.5" fill="#fff"/></svg></li>
      <li>www.brellhaulage-example.com.au <svg class="contact-icon" viewBox="0 0 8 8"><circle cx="4" cy="4" r="3.3" fill="none" stroke="#fff" stroke-width=".9"/><path d="M.8,4 H7.2 M4,.8 V7.2" stroke="#fff" stroke-width=".6"/></svg></li>
      <li>P.O Box 817 Wattlegrove WA, 6958 <svg class="contact-icon" viewBox="0 0 8 8"><path d="M4,.5 L7.5,4 L6.3,4 L6.3,7.5 L1.7,7.5 L1.7,4 L.5,4 Z" fill="#fff"/></svg></li>
    </ul>
    <footer class="legal-footer">
      <p class="abn">ABN 71 834 209 553</p>
      <p class="entity">Brell Holdings Pty Ltd (ACN 582 316 907) ATF The Brell Discretionary Trust T/AS</p>
    </footer>
  </article>

  <p class="option-label option-label--one">Option 1</p>
  <p class="option-label option-label--two">Option 2</p>
</div>
</body>
</html>
```